Irrigation Business needs their business cards modernised and revamped

I would like to keep my current logo, colours and revamp the format of the card.

I would like the card to be clean yet important.

Im not sure if you include texture but i would like the named logo to be indented into the card etc.

show me something alive and free something thats clinical to the point yet has a feel of achievement. i would like people to go nice card.

Target Market(s)

high end clients, corporate, sports field manger, the guys that make the decisions

Industry/Entity Type

Business

Contact Information for Business Card

nformation to be included

Dean Harlow (Director)
0487305526
dean@kolvat.biz
www.kestonfieldworks.com

instagram logo
google logo
facebook logo

Colors

Designer to choose colors to be used in the design.

Requirements
Nice to have
• indentations a really nice feel to the card good texture

```html
<!DOCTYPE html>
<html lang="en">
<head>
<meta charset="utf-8">
<title>Keston Fieldworks – Business Card</title>
<link rel="stylesheet" href="https://fonts.googleapis.com/css2?family=Roboto:wght@400;700;900&display=swap">
<style>
  :root {
    --stage: #e9e9ea;
    --card: #f6f7f8;
    --navy: #2e4a8c;
    --sky: #3a8fcb;
    --green: #1e9a4c;
    --ink: #333a44;
    --white: #ffffff;
    --social-a: #b8358f;
    --social-b: #d9503f;
    --social-c: #2f62ad;
  }
  * { box-sizing: border-box; margin: 0; padding: 0; }
  html, body { width: 1200px; height: 576px; overflow: hidden; }
  body {
    background: var(--stage);
    font-family: "Roboto", Arial, sans-serif;
    position: relative;
  }
  .card {
    position: absolute;
    top: 138px;
    width: 484px;
    height: 294px;
    background: linear-gradient(160deg, #fbfbfc 0%, var(--card) 60%, #eef0f2 100%);
    border-radius: 12px;
    box-shadow: 0 3px 6px rgba(0,0,0,.18);
    overflow: hidden;
  }
  .card--front { left: 82px; }
  .card--back { left: 602px; width: 481px; }

  .brand { position: absolute; text-align: center; }
  .brand__dot { display: block; margin: 0 auto; border-radius: 50%; background: var(--sky); }
  .brand__name {
    display: block;
    color: var(--navy);
    font-weight: 900;
    letter-spacing: -.5px;
    white-space: nowrap;
  }
  .card--front .brand { left: 0; right: 0; top: 56px; }
  .card--front .brand__dot { width: 92px; height: 92px; }
  .card--front .brand__name { font-size: 30px; margin-top: 20px; }

  .card--back .brand { left: 22px; width: 240px; top: 40px; }
  .card--back .brand__dot { width: 112px; height: 112px; }
  .card--back .brand__name { font-size: 26px; margin-top: 24px; }

  .social { display: flex; gap: 6px; }
  .social__dot { width: 16px; height: 16px; border-radius: 50%; }
  .social__dot--a { background: var(--social-a); }
  .social__dot--b { background: var(--social-b); }
  .social__dot--c { background: var(--social-c); }
  .card--back .social__dot { width: 19px; height: 19px; }

  .front-rule {
    position: absolute; left: 80px; right: 80px; top: 263px;
    display: flex; align-items: center; gap: 10px;
  }
  .front-rule__line { flex: 1; height: 2px; background: var(--navy); }

  .wave { position: absolute; inset: 0; }

  .person { position: absolute; right: 23px; top: 167px; text-align: right; }
  .person { top: 40px; }
  .person__name { color: var(--navy); font-weight: 700; font-size: 22px; letter-spacing: .2px; }
  .person__role { color: var(--ink); font-size: 11.5px; margin-top: 4px; }
  .person .social { justify-content: flex-end; margin-top: 14px; }

  .contact {
    position: absolute; right: 24px; top: 219px;
    list-style: none; text-align: right; color: var(--white);
    font-size: 12.5px; line-height: 16.5px;
  }
  .contact__item { display: flex; justify-content: flex-end; align-items: center; gap: 7px; }
  .contact__icon { width: 10px; height: 10px; fill: #cfd9ee; }
</style>
</head>
<body>

<section class="card card--front" aria-label="Card front">
  <div class="brand">
    <span class="brand__dot"></span>
    <span class="brand__name">KESTON FIELDWORKS</span>
  </div>
  <div class="front-rule">
    <span class="front-rule__line"></span>
    <div class="social" aria-label="Social channels">
      <span class="social__dot social__dot--a"></span>
      <span class="social__dot social__dot--b"></span>
      <span class="social__dot social__dot--c"></span>
    </div>
    <span class="front-rule__line"></span>
  </div>
</section>

<section class="card card--back" aria-label="Card back">
  <svg class="wave" viewBox="0 0 481 294" preserveAspectRatio="none" aria-hidden="true">
    <path d="M0 252 C 110 268, 230 240, 330 205 C 400 180, 450 168, 481 166 L481 294 L0 294 Z" fill="var(--navy)"/>
    <path d="M60 242 C 170 262, 280 225, 360 190 C 410 168, 450 150, 481 147 L481 158 C 450 160, 410 176, 360 200 C 280 238, 170 268, 60 242 Z" fill="var(--sky)"/>
    <path d="M0 232 C 90 236, 180 240, 270 238 C 200 252, 90 262, 0 250 Z" fill="var(--green)"/>
  </svg>

  <div class="brand">
    <span class="brand__dot"></span>
    <span class="brand__name">KESTON FIELDWORKS</span>
  </div>

  <div class="person">
    <p class="person__name">DEAN HARLOW</p>
    <p class="person__role">Director</p>
    <div class="social" aria-label="Social channels">
      <span class="social__dot social__dot--a"></span>
      <span class="social__dot social__dot--b"></span>
      <span class="social__dot social__dot--c"></span>
    </div>
  </div>

  <ul class="contact">
    <li class="contact__item">0487305526
      <svg class="contact__icon" viewBox="0 0 10 10"><path d="M1 3 Q5 0 9 3 L8 4.5 L6.5 4 L6.5 3 Q5 2.6 3.5 3 L3.5 4 L2 4.5 Z M2 5.5 L8 5.5 L9 9 L1 9 Z"/></svg>
    </li>
    <li class="contact__item">dean@kolvat.biz
      <svg class="contact__icon" viewBox="0 0 10 10"><path d="M0 2 H10 V8.5 H0 Z M0.8 2.6 L5 5.6 L9.2 2.6 Z" fill-rule="evenodd"/></svg>
    </li>
    <li class="contact__item">www.kestonfieldworks.com
      <svg class="contact__icon" viewBox="0 0 10 10"><circle cx="5" cy="5" r="4.3" fill="none" stroke="#cfd9ee" stroke-width="1"/><path d="M0.7 5 H9.3 M5 0.7 V9.3" stroke="#cfd9ee" stroke-width=".8"/></svg>
    </li>
  </ul>
</section>

</body>
</html>
```